Need Business Card for our Real Estate Business with Sales Executive's Picture

PANTONE 484 C ( RED)

PANTONE 2766 C ( BLUE

Industry/Entity Type

Real Estate

Contact Information for Business Card

Name, Mobile, email, & picture of Person
Agency Phone, address, Web address

Requirements
Must have
• Our Logo Colours, Agent Picture,

```html
<!DOCTYPE html>
<html lang="en">
<head>
<meta charset="utf-8">
<title>Corveth Real Estate – Business Card</title>
<link href="https://fonts.googleapis.com/css2?family=Work+Sans:wght@400;500;600&display=swap" rel="stylesheet">
<style>
  :root {
    --navy: #0f1a47;
    --red: #7a1420;
    --paper: #ffffff;
    --ink-soft: #4a4f5c;
    --backdrop: #3b3b3d;
    --photo-light: #e9eaf0;
    --photo-mid: #2b4a9a;
  }
  * { margin: 0; padding: 0; box-sizing: border-box; }
  html, body { width: 1200px; height: 900px; overflow: hidden; }
  body {
    background: var(--backdrop);
    font-family: "Work Sans", Arial, sans-serif;
    position: relative;
  }
  .card {
    position: absolute;
    left: 250px;
    width: 700px;
    height: 400px;
    background: var(--paper);
    overflow: hidden;
  }
  .card--front { top: 40px; }
  .card--back { top: 460px; }

  /* Front */
  .portrait {
    position: absolute;
    left: 0; top: 0;
    width: 340px; height: 400px;
    background: linear-gradient(160deg, var(--photo-light) 0%, var(--photo-light) 30%, var(--photo-mid) 70%, #1d3272 100%);
  }
  .brand {
    position: absolute;
    display: flex;
    align-items: center;
    gap: 12px;
    color: var(--navy);
    font-weight: 500;
  }
  .brand__square {
    width: 12px; height: 12px;
    background: var(--red);
    flex: none;
  }
  .brand__name { line-height: 1.05; letter-spacing: 0.08em; text-transform: uppercase; }
  .brand__name span { display: block; font-size: 0.32em; letter-spacing: 0.3em; margin-top: 6px; }
  .card--front .brand { left: 400px; top: 165px; font-size: 46px; }
  .card--back .brand { left: 40px; top: 45px; font-size: 40px; }

  /* Back */
  .card-lines { position: absolute; inset: 0; }
  .contact-list {
    position: absolute;
    left: 40px; top: 236px;
    list-style: none;
    font-size: 16px;
    color: var(--ink-soft);
    line-height: 1.45;
  }
  .contact-list li { display: flex; align-items: center; gap: 12px; }
  .contact-list svg { width: 12px; height: 12px; flex: none; }
  .person {
    position: absolute;
    right: 74px; top: 262px;
    text-align: right;
  }
  .person__name {
    font-size: 28px; font-weight: 600;
    color: var(--navy);
    letter-spacing: 0.02em;
    text-transform: uppercase;
    line-height: 1.2;
  }
  .person__role {
    font-size: 19px; font-weight: 400;
    color: var(--red);
    letter-spacing: 0.03em;
    line-height: 1.3;
  }
  .address {
    position: absolute;
    left: 370px; top: 338px;
    color: var(--paper);
    font-size: 19px;
    line-height: 1.25;
    letter-spacing: 0.02em;
  }
</style>
</head>
<body>

<section class="card card--front" aria-label="Card front">
  <div class="portrait" role="img" aria-label="Portrait photo of the managing director in a blue suit"></div>
  <div class="brand">
    <div class="brand__name">Corveth<span>Real Estate</span></div>
    <div class="brand__square"></div>
  </div>
</section>

<section class="card card--back" aria-label="Card back">
  <svg class="card-lines" width="700" height="400" viewBox="0 0 700 400">
    <line x1="40" y1="130" x2="420" y2="298" stroke="#0f1a47" stroke-width="1.5"/>
    <polygon points="0,384 240,394 236,400 0,400" fill="#7a1420"/>
    <polygon points="250,400 300,332 700,332 700,400" fill="#0f1a47"/>
    <rect x="640" y="262" width="5" height="42" fill="#7a1420"/>
    <rect x="652" y="262" width="48" height="42" fill="#0f1a47"/>
  </svg>

  <div class="brand">
    <div class="brand__name">Corveth<span>Real Estate</span></div>
    <div class="brand__square"></div>
  </div>

  <ul class="contact-list">
    <li><svg viewBox="0 0 12 12"><path d="M2 1h3l1 3-2 1a6 6 0 0 0 3 3l1-2 3 1v3c-6 0-9-3-9-9z" fill="#4a4f5c"/></svg>+852 2740 1185</li>
    <li><svg viewBox="0 0 12 12"><rect x="1" y="2" width="10" height="8" rx="1" fill="#4a4f5c"/></svg>+852 2740 1196</li>
    <li><svg viewBox="0 0 12 12"><rect x="1" y="2.5" width="10" height="7" fill="none" stroke="#4a4f5c"/><path d="M1 3l5 4 5-4" fill="none" stroke="#4a4f5c"/></svg>info@corvethrealty.com</li>
    <li><svg viewBox="0 0 12 12"><circle cx="6" cy="6" r="5" fill="none" stroke="#4a4f5c"/><path d="M1 6h10M6 1v10" stroke="#4a4f5c"/></svg>www.corvethrealty.com</li>
  </ul>

  <div class="person">
    <div class="person__name">Daniel Reeve</div>
    <div class="person__role">Managing Director</div>
  </div>

  <div class="address">Via Monte Rosa,<br>148. 12030 Borgo (CN)</div>
</section>

</body>
</html>
```